Business Card Design for my Real Estate Investing Company

This is for a Real Estate Investing Company that will be serving the Las Vegas Valley. Id like the following slogan included: "Investing in Our Community" I have attached my logo. You will see the color tones I'm interested in..in my logo. I would like the card to be double-sided with a modern, professional look.
Target Market(s)
Homeowners, banks, real estate industry
Industry/Entity Type
Real Estate
Contact Information for Business Card
name: Dale Harwick
position: Managing Member
address: 4821 Corliss Pkwy ste 207-300
N. Las Vegas, NV 89084
phone: (702) 555-0143
fax: (702) 555-0187
email: SummitRidgeEstate@hollowmail.test
web: SummitRidgeEstates.test
*At the bottom of the card I would like....
We buy houses for cash....no repairs, no commissions, no fees!
Logo Text
SUMMIT RIDGE ESTATES "Investing in Our Community"
Font styles to use
Other font styles liked:
- Lora
Requirements
Must have
- On the back of the card, i'd like to have my logo large and the following statements:
- Are you considering selling your home? Want a simple, hassle-free transaction? We can help! We buy houses for cash and can close quickly! No need to do any repairs, no realtor commissions, no closing costs.....and no headaches. Let us help you with your real estate needs...!
Nice to have
- multiple colors 2 two tone on front and back

```html
<!DOCTYPE html>
<html lang="en">
<head>
<meta charset="utf-8">
<title>Summit Ridge Estates – Business Card</title>
<link rel="stylesheet" href="https://fonts.googleapis.com/css2?family=Lora:ital,wght@0,400;0,700;1,400&family=Open+Sans:wght@400;600&display=swap">
<style>
  :root {
    --backdrop: #3a3330;
    --card: #232325;
    --card-edge: #1b1b1d;
    --blue: #1565c8;
    --grey: #a7a9ac;
    --text: #f2f2f2;
    --muted: #c9c9c9;
  }
  * { box-sizing: border-box; margin: 0; padding: 0; }
  html, body { width: 1200px; height: 844px; overflow: hidden; }
  body {
    background: var(--backdrop);
    display: flex;
    align-items: center;
    justify-content: center;
    gap: 40px;
    font-family: "Open Sans", Arial, sans-serif;
  }
  .card {
    position: relative;
    width: 540px;
    height: 309px;
    background: var(--card);
    border: 1px solid var(--card-edge);
    box-shadow: 0 10px 24px rgba(0,0,0,.45);
    overflow: hidden;
    color: var(--text);
  }

  /* Front */
  .front .band-top { position: absolute; left: 0; right: 0; top: 0; height: 10px; background: var(--blue); }
  .front .band-bottom { position: absolute; left: 0; right: 0; bottom: 0; height: 12px; background: var(--blue); }
  .front .details { position: absolute; left: 0; right: 0; top: 42px; text-align: center; }
  .person-name {
    font-family: "Lora", Georgia, serif;
    font-weight: 700;
    color: var(--blue);
    font-size: 19px;
    letter-spacing: .5px;
    text-transform: uppercase;
  }
  .person-role { font-size: 13px; color: var(--muted); margin-top: 2px; }
  .contact { margin-top: 26px; font-size: 14px; line-height: 1.5; }
  .contact .label { color: var(--blue); font-weight: 600; }
  .address { margin-top: 18px; font-size: 14px; }
  .slogan {
    position: absolute; left: 0; right: 0; bottom: 32px;
    text-align: center;
    font-family: "Lora", Georgia, serif;
    font-style: italic;
    color: var(--blue);
    font-size: 18px;
  }

  /* Back */
  .back .bar-right { position: absolute; right: 0; top: 22px; width: 14px; height: 56px; background: var(--blue); }
  .back .bar-right::before { content: ""; position: absolute; left: -5px; top: 0; width: 5px; height: 100%; background: var(--grey); }
  .back .bar-left { position: absolute; left: 0; bottom: 40px; width: 16px; height: 66px; background: var(--blue); }
  .back .bar-left::after { content: ""; position: absolute; right: -5px; top: 0; width: 5px; height: 100%; background: var(--grey); }
  .brand { position: absolute; left: 0; right: 0; top: 52px; text-align: center; }
  .brand-name {
    font-family: "Lora", Georgia, serif;
    font-weight: 700;
    color: var(--blue);
    font-size: 30px;
    letter-spacing: 1px;
  }
  .brand-tagline {
    font-family: "Lora", Georgia, serif;
    color: var(--grey);
    font-size: 12px;
    letter-spacing: 2px;
    margin-top: 4px;
  }
  .pitch {
    position: absolute; left: 50px; right: 50px; top: 140px;
    text-align: center;
    font-size: 13px;
    line-height: 1.55;
    color: var(--text);
  }
</style>
</head>
<body>
  <section class="card front" aria-label="Card front">
    <div class="band-top"></div>
    <div class="details">
      <h1 class="person-name">Dale Harwick</h1>
      <p class="person-role">Managing Member</p>
      <div class="contact">
        <p><span class="label">P:</span> (702) 555-0143 | <span class="label">F:</span> (702) 555-0187</p>
        <p><span class="label">E:</span> SummitRidgeEstate@hollowmail.test</p>
        <p><span class="label">W:</span> SummitRidgeEstates.test</p>
      </div>
      <p class="address">4821 Corliss Pkwy ste 207-300 N. Las Vegas, NV 89084</p>
    </div>
    <p class="slogan">We buy houses for cash....no repairs, no commissions, no fees!</p>
    <div class="band-bottom"></div>
  </section>

  <section class="card back" aria-label="Card back">
    <div class="bar-right"></div>
    <div class="brand">
      <h2 class="brand-name">SUMMIT RIDGE ESTATES</h2>
      <p class="brand-tagline">"Investing in Our Community"</p>
    </div>
    <p class="pitch">Are you considering selling your home?<br>
      Want a simple, hassle-free transaction?<br>
      We can help! We buy houses for cash and<br>
      can close quickly! No need to do any repairs,<br>
      no realtor commissions, no closing costs.....<br>
      and no headaches. Let us help you with your real estate needs...!</p>
    <div class="bar-left"></div>
  </section>
</body>
</html>
```